Sophisticated, clean website reflecting my feminine, playful side to sell my abstract art,

I need a website no more than 3 pages to showcase my paintings, a little about me and some contact info. I do abstracts so looking for something a little edgy, yet feminine and current.
Updates

Hi there, These are some artists websites that I Iike: Marnelvoss.com (I like how airy it is) peterwallombry.com garethpolvens.com (I like how it scrolls) I'll need a place for a photo ( a headshot-i do not have it yet so I'll need to be able to upload that later) as well as an area for my bio. Also, it's important that I will be able to upload any new photos and descriptions easily so it should be user friendly. Lastly, I like in a sunny place so would like to have this seem upbeat and playful as that is how i like to paint. thanks-I'm trying to upload my photos now -

Target Market(s)

ppl ages 35-70 who want large scale art for their homes

Industry/Entity Type

art

Coding

Coded - Design and coding required

Number of Pages Required

3 page

Colors

Designer to choose colors to be used in the design.

Requirements
Must have
• photos of my art, a place for my bio, be easy to reach me. tasteful-nothing too "in your face" -my clients are pretty high end and organized. They like clean lines
Nice to have
• sophisticated background, muted tones in the back-similar clean font throughout-no cursive
Should not have
• too many dark areas. Too many blocks of color. Too serious.

```html
<!DOCTYPE html>
<html lang="en">
<head>
<meta charset="utf-8">
<title>ELWINART — Abstract Paintings</title>
<link href="https://fonts.googleapis.com/css2?family=EB+Garamond:wght@400;500&family=Poppins:wght@300;400&display=swap" rel="stylesheet">
<style>
  :root{
    --accent:#c0735f;
    --ink:#1b1b1b;
    --text:#2a2a2a;
    --frame:#c4a47f;
    --panel:#dcd2c0;
    --footer:#c3a889;
    --footer-head:#f3e6d6;
    --white:#ffffff;
    --muted:#9a9a9a;
  }
  *{box-sizing:border-box;margin:0;padding:0}
  html,body{width:1200px;height:3701px;overflow:hidden;background:var(--white)}
  body{position:relative;font-family:"EB Garamond",Georgia,serif;color:var(--text)}
  .abs{position:absolute}
  .btn{position:absolute;background:var(--accent);color:var(--white);display:flex;align-items:center;justify-content:center;font-size:16px;letter-spacing:.5px}

  /* header */
  .site-header{left:0;top:0;width:1200px;height:86px;background:var(--white);box-shadow:0 6px 18px rgba(0,0,0,.08);z-index:2}
  .brand-mark{left:66px;top:11px;width:64px;height:64px;background:var(--ink);border:2px solid var(--frame)}
  .brand-name{left:147px;top:18px;font-size:33px;letter-spacing:1.5px;color:var(--ink);line-height:44px}
  .nav-link{top:26px;font-size:19px;color:var(--ink);line-height:28px}
  .nav-cta{left:994px;top:23px;width:111px;height:36px;font-size:18px}

  /* hero */
  .hero{left:0;top:86px;width:1200px;height:579px;
    background:radial-gradient(ellipse at 62% 40%,#8e2d1e 0%,#b4573f 18%,rgba(214,170,150,.8) 38%,rgba(232,226,226,0) 60%),
               radial-gradient(ellipse at 2% 85%,#8a3a1c 0%,#c27a52 18%,rgba(230,222,222,0) 38%),
               linear-gradient(100deg,#e7e3e4 0%,#ded9da 70%,#c9a57e 92%,#b89470 100%)}
  .hero-arrow{top:357px;width:36px;height:36px;background:var(--white)}

  /* about */
  .portrait-frame{left:161px;top:793px;width:306px;height:377px;border:3px solid var(--frame)}
  .eyebrow{font-size:22px;color:var(--accent);line-height:28px}
  .section-title{font-size:34px;color:var(--ink);letter-spacing:1.5px;line-height:40px;font-weight:400}
  .copy{font-size:16.3px;line-height:19px;color:var(--text)}
  .copy p+p{margin-top:19px}

  /* gallery */
  .centered-title{left:0;width:1200px;text-align:center;font-size:33px;color:var(--ink);line-height:40px;font-weight:400;letter-spacing:.5px}
  .product-card{top:1305px;width:200px;height:274px;background:var(--white);box-shadow:0 2px 10px rgba(0,0,0,.16)}
  .product-art{position:absolute;left:16px;top:13px;width:167px;height:171px}
  .product-name{position:absolute;left:0;top:191px;width:180px;text-align:center;font-size:14px;color:var(--ink)}
  .product-price{position:absolute;left:0;top:217px;width:180px;text-align:center;font-size:11px;color:var(--ink)}
  .product-price s{color:var(--muted);margin-right:6px;font-size:9px}
  .product-btn{position:absolute;left:57px;top:240px;width:85px;height:17px;background:var(--accent);color:var(--white);font-size:9px;display:flex;align-items:center;justify-content:center;letter-spacing:.3px}

  /* contact */
  .contact-card{left:59px;top:2209px;width:1076px;height:448px;background:var(--white);box-shadow:0 6px 30px rgba(0,0,0,.09)}
  .form-panel{left:141px;top:2252px;width:330px;height:361px;background:var(--panel)}
  .form-lead{left:168px;top:2288px;width:290px;color:var(--white);font-size:17px;line-height:19px}
  .field{left:168px;width:277px;height:22px;background:var(--white);font-size:8.5px;color:var(--muted);padding:5px 14px}

  /* instagram */
  .feed-tile{}

  /* footer */
  .site-footer{left:0;top:3350px;width:1200px;height:351px;background:var(--footer)}
  .footer-mark{left:116px;top:3393px;width:101px;height:100px;background:var(--ink)}
  .footer-about{left:116px;top:3516px;width:250px;font-family:"Poppins",sans-serif;font-weight:300;font-size:10.5px;line-height:18px;color:var(--white)}
  .social{top:3596px;width:18px;height:18px;border:1.5px solid var(--white);border-radius:50%}
  .footer-head{top:3430px;font-size:23px;color:var(--footer-head);letter-spacing:.5px;line-height:28px}
  .footer-link{font-family:"Poppins",sans-serif;font-weight:300;font-size:13px;color:var(--white);line-height:18px}
  .bullet{width:6px;height:6px;border-radius:50%;background:var(--white)}
  .footer-contact{left:974px;font-family:"Poppins",sans-serif;font-weight:400;font-size:17px;color:var(--white);line-height:24px}
  .footer-rule{left:116px;top:3640px;width:984px;height:1px;background:rgba(255,255,255,.5)}
  .copyright{left:0;top:3657px;width:1200px;text-align:center;font-family:"Poppins",sans-serif;font-weight:300;font-size:13px;color:var(--white)}
</style>
</head>
<body>

<header class="abs site-header">
  <div class="abs brand-mark" aria-hidden="true"></div>
  <div class="abs brand-name">ELWINART</div>
  <nav>
    <span class="abs nav-link" style="left:568px">Home</span>
    <span class="abs nav-link" style="left:655px">About me</span>
    <span class="abs nav-link" style="left:775px">showcase my paintings</span>
    <span class="btn nav-cta">Contact us</span>
  </nav>
</header>

<section>
  <div class="abs hero" role="img" aria-label="Close view of an abstract painting with rust and deep red brush swirls on white canvas"></div>
  <div class="abs hero-arrow" style="left:17px">
    <svg width="36" height="36" viewBox="0 0 36 36"><path d="M26 18H10M16 12l-6 6 6 6" fill="none" stroke="#1b1b1b" stroke-width="2"/></svg>
  </div>
  <div class="abs hero-arrow" style="left:1147px">
    <svg width="36" height="36" viewBox="0 0 36 36"><path d="M10 18h16M20 12l6 6-6 6" fill="none" stroke="#1b1b1b" stroke-width="2"/></svg>
  </div>
</section>

<section class="about">
  <div class="abs portrait-frame" role="img" aria-label="Space for the artist's portrait"></div>
  <div class="abs eyebrow" style="left:616px;top:806px">About</div>
  <h2 class="abs section-title" style="left:614px;top:840px">ELWINART</h2>
  <div class="abs copy" style="left:614px;top:886px;width:480px">
    <p>Lorem ipsum dolor sit amet, consectetur estor adipi isicing elit, sed do eiusmod tempor este uterre incididui unt ut labore et dolore magna aliquaas. Ut enim ad minim veniam, quis mot nostrud desto exercitation est ullamco laboris nisi ut se aliquip ex ea commodos consequat.</p>
    <p>Duis aute irure et dolor in reprehender itinse voluptate velit esse cillum dolore eu fugiat do nulla pariatur deus ex. Excepteur sint occaecat er cupidatat non ullamco proident, sunt in dos<br>Lorem ipsum dolor sit amet, consectetur adipisic eli sed do eiusmod tempor incididunt ut labore et dolore si magna</p>
  </div>
  <span class="btn" style="left:614px;top:1089px;width:129px;height:38px">Contact us</span>
</section>

<section class="gallery">
  <h2 class="abs centered-title" style="top:1219px">Gallery</h2>
  <div class="abs product-card" style="left:63px">
    <div class="product-art" role="img" aria-label="Abstract painting in ochre, blue and white" style="background:linear-gradient(135deg,#c28a2a,#e7dccb 45%,#3f5f8a 75%,#b8752a)"></div>
    <div class="product-name">Lorem ipsum</div>
    <div class="product-price"><s>$ 45.000</s>$ 35.000</div>
    <div class="product-btn">ADD TO CART</div>
  </div>
  <div class="abs product-card" style="left:282px">
    <div class="product-art" role="img" aria-label="Abstract painting in violet and blue" style="background:linear-gradient(135deg,#e3ddd8,#7a62b0 45%,#2e3c7a 70%,#d9d2cc)"></div>
    <div class="product-name">Lorem ipsum</div>
    <div class="product-price"><s>$ 45.000</s>$ 35.000</div>
    <div class="product-btn">ADD TO CART</div>
  </div>
  <div class="abs product-card" style="left:500px">
    <div class="product-art" role="img" aria-label="Abstract painting with rust red swirls" style="background:linear-gradient(135deg,#e6dfdc,#a8432c 45%,#d9b3a2 75%,#b48a63)"></div>
    <div class="product-name">Lorem ipsum</div>
    <div class="product-price"><s>$ 45.000</s>$ 35.000</div>
    <div class="product-btn">ADD TO CART</div>
  </div>
  <div class="abs product-card" style="left:719px">
    <div class="product-art" role="img" aria-label="Abstract painting in teal, orange and black" style="background:linear-gradient(135deg,#c07a3a,#1f8a80 40%,#2b2b2b 65%,#d9d4cc)"></div>
    <div class="product-name">Lorem ipsum</div>
    <div class="product-price"><s>$ 45.000</s>$ 35.000</div>
    <div class="product-btn">ADD TO CART</div>
  </div>
  <div class="abs product-card" style="left:937px">
    <div class="product-art" role="img" aria-label="Abstract painting in teal, orange and black" style="background:linear-gradient(135deg,#c07a3a,#1f8a80 40%,#2b2b2b 65%,#d9d4cc)"></div>
    <div class="product-name">Lorem ipsum</div>
    <div class="product-price"><s>$ 45.000</s>$ 35.000</div>
    <div class="product-btn">ADD TO CART</div>
  </div>
  <span class="btn" style="left:536px;top:1630px;width:129px;height:36px">Explore More</span>
</section>

<section class="works">
  <div class="abs eyebrow" style="left:59px;top:1774px">The Museum archive</div>
  <h2 class="abs section-title" style="left:59px;top:1810px">WORKS OF ART</h2>
  <div class="abs copy" style="left:59px;top:1864px;width:484px">
    <p>Lorem ipsum dolor sit amet, consectetur estor adipi isicing elit, sed do eiusmod tempor este uterre incididui unt ut labore et dolore magna aliquaas. Ut enim ad minim veniam, quis mot nostrud desto exercitation est ullamco laboris nisi ut se aliquip ex ea commodos consequat.</p>
    <p>Duis aute irure et dolor in reprehender itinse voluptate velit esse cillum dolore eu fugiat do nulla pariatur deus ex. Excepteur sint occaecat er cupidatat non ullamco proident, sunt in dos<br>Lorem ipsum dolor sit amet, consectetur adipisic eli sed do eiusmod tempor incididunt ut labore et dolore si magna aliqua. Ut enim adese</p>
  </div>
  <span class="btn" style="left:59px;top:2087px;width:128px;height:34px">Contact us</span>
  <div class="abs" style="left:703px;top:1760px;width:432px;height:367px;background:radial-gradient(circle at 35% 50%,#c98a84 0%,#e2b8ae 30%,#d9c7bb 55%,#5a2f35 85%,#3b1f25 100%)" role="img" aria-label="Abstract painting of pink roses with dark leaves"></div>
</section>

<section class="contact">
  <div class="abs contact-card"></div>
  <div class="abs form-panel"></div>
  <div class="abs form-lead">Fill the form if you want to get more information about painting</div>
  <div class="abs field" style="top:2352px">Enter Your Name</div>
  <div class="abs field" style="top:2385px">Enter Your Email</div>
  <div class="abs field" style="top:2420px">Enter Your Number</div>
  <div class="abs field" style="top:2454px;height:91px">write massage</div>
  <span class="btn" style="left:168px;top:2561px;width:68px;height:29px;font-size:17px">Send</span>
  <h2 class="abs section-title" style="left:601px;top:2298px;font-size:33px;letter-spacing:.5px">Get in Touch</h2>
  <div class="abs copy" style="left:605px;top:2360px;width:490px">
    <p>Lorem ipsum dolor sit amet, consectetur estor adipi isicing elit, sed do eiusmod tempor este uterre incididui unt ut labore et dolore magna aliquaas. Ut enim ad minim veniam, quis mot nostrud desto exercitation est ullamco laboris nisi ut se aliquip ex ea commodos consequat.</p>
    <p>Duis aute irure et dolor in reprehender itinse voluptate velit esse cillum dolore eu fugiat do nulla pariatur deus ex. Excepteur sint occaecat er cupidatat non ullamco proident, sunt in dos Lorem ipsum dolor sit amet, consectetur adipisic eli sed do eiusmod tempor incididunt ut labore et dolore si magna aliqua. Ut enim adese</p>
  </div>
</section>

<section class="instagram">
  <h2 class="abs centered-title" style="top:2725px">Instagram</h2>
  <div class="abs feed-tile" style="left:90px;top:2798px;width:284px;height:211px;background:linear-gradient(135deg,#e9e3e0,#a23a25 45%,#e3d2cc 75%,#9b7a57)" role="img" aria-label="Rust red abstract painting"></div>
  <div class="abs feed-tile" style="left:394px;top:2798px;width:214px;height:158px;background:linear-gradient(135deg,#c89a2e,#eee7dc 45%,#3f6aa0 70%,#b8822a)" role="img" aria-label="Ochre and blue abstract painting"></div>
  <div class="abs feed-tile" style="left:398px;top:2967px;width:208px;height:252px;background:linear-gradient(160deg,#d1a033,#efe9df 35%,#5877a8 60%,#c98b2f 85%,#f0ebe4)" role="img" aria-label="Ochre and blue abstract painting with repeated rose shapes"></div>
  <div class="abs feed-tile" style="left:624px;top:2798px;width:175px;height:231px;background:linear-gradient(135deg,#5c3a4a,#d7a9a0 40%,#e8ddd5 60%,#7a4a55)" role="img" aria-label="Pink and plum rose abstract painting"></div>
  <div class="abs feed-tile" style="left:812px;top:2798px;width:296px;height:231px;background:linear-gradient(135deg,#6f5fa0,#e2d8cc 40%,#3c3f78 65%,#d9cfc4)" role="img" aria-label="Violet and navy abstract painting"></div>
  <div class="abs feed-tile" style="left:89px;top:3019px;width:285px;height:200px;background:linear-gradient(135deg,#d9d6d0,#1f8a80 40%,#2a2a2a 60%,#c77a3a 85%)" role="img" aria-label="Teal and black burst abstract painting"></div>
  <div class="abs feed-tile" style="left:624px;top:3041px;width:234px;height:178px;background:linear-gradient(135deg,#e8e6dc,#2f8f58 40%,#1a6b7a 65%,#c6b35a)" role="img" aria-label="Green and blue abstract painting"></div>
  <div class="abs feed-tile" style="left:869px;top:3041px;width:242px;height:178px;background:linear-gradient(90deg,#1a78a8,#6fb6cf 30%,#e3dcd2 60%,#c9b7a0)" role="img" aria-label="Blue drip abstract painting on beige"></div>
  <span class="btn" style="left:536px;top:3262px;width:129px;height:36px">Explore More</span>
</section>

<footer class="abs site-footer"></footer>
<div class="abs footer-mark" aria-hidden="true"></div>
<div class="abs footer-about">lorem ipsum dolor sit amet, consectetur adipiscing elit, viverra et pellentesque leo imperdiet quis. a diam ut natoque amet sodales. id amet, viverra vitae et enim.</div>
<span class="abs social" style="left:123px" aria-label="Social link"></span>
<span class="abs social" style="left:166px" aria-label="Social link"></span>
<span class="abs social" style="left:208px" aria-label="Social link"></span>
<span class="abs social" style="left:253px" aria-label="Social link"></span>

<div class="abs footer-head" style="left:411px">QUCIK LINKS</div>
<span class="abs bullet" style="left:412px;top:3515px"></span><span class="abs footer-link" style="left:443px;top:3509px">Home</span>
<span class="abs bullet" style="left:412px;top:3541px"></span><span class="abs footer-link" style="left:443px;top:3535px">About me</span>
<span class="abs bullet" style="left:412px;top:3565px"></span><span class="abs footer-link" style="left:443px;top:3558px">Showcase My Paintings</span>
<span class="abs bullet" style="left:412px;top:3590px"></span><span class="abs footer-link" style="left:443px;top:3583px">Contact us</span>

<div class="abs footer-head" style="left:660px">CUSTOMER CARE</div>
<span class="abs bullet" style="left:660px;top:3486px"></span><span class="abs footer-link" style="left:693px;top:3479px">gift card balance</span>
<span class="abs bullet" style="left:660px;top:3512px"></span><span class="abs footer-link" style="left:693px;top:3505px">Acount</span>
<span class="abs bullet" style="left:660px;top:3539px"></span><span class="abs footer-link" style="left:693px;top:3532px">Shipping Policy</span>
<span class="abs bullet" style="left:660px;top:3567px"></span><span class="abs footer-link" style="left:693px;top:3560px">Care &amp; Repair</span>
<span class="abs bullet" style="left:660px;top:3594px"></span><span class="abs footer-link" style="left:693px;top:3587px">FAQ</span>

<div class="abs footer-head" style="left:936px">CONTACT US</div>
<svg class="abs" style="left:935px;top:3476px" width="20" height="20" viewBox="0 0 24 24"><path d="M6.6 10.8a15 15 0 006.6 6.6l2.2-2.2a1 1 0 011-.25 11.4 11.4 0 003.6.57 1 1 0 011 1V20a1 1 0 01-1 1A17 17 0 013 4a1 1 0 011-1h3.5a1 1 0 011 1c0 1.25.2 2.45.57 3.6a1 1 0 01-.25 1z" fill="#fff"/></svg>
<span class="abs footer-contact" style="top:3474px">080-555-014</span>
<svg class="abs" style="left:935px;top:3521px" width="22" height="16" viewBox="0 0 22 16"><rect x="1" y="1" width="20" height="14" fill="none" stroke="#fff" stroke-width="1.3"/><path d="M1 1l10 8 10-8" fill="none" stroke="#fff" stroke-width="1.3"/></svg>
<span class="abs footer-contact" style="top:3517px">Email Us</span>
<svg class="abs" style="left:937px;top:3561px" width="18" height="24" viewBox="0 0 18 24"><path d="M9 1a7.5 7.5 0 00-7.5 7.5C1.5 14 9 23 9 23s7.5-9 7.5-14.5A7.5 7.5 0 009 1z" fill="none" stroke="#fff" stroke-width="1.4"/><circle cx="9" cy="8.5" r="2.6" fill="none" stroke="#fff" stroke-width="1.4"/></svg>
<span class="abs footer-contact" style="top:3561px">Get Direction</span>

<div class="abs footer-rule"></div>
<div class="abs copyright">Copyright elwinart 2021 All Rights Reserved</div>

</body>
</html>
```